Looking for a modern, Professional business card design

We have a simple business card, but are looking for a more modern, professional look. A sample of the basic card is attached as well as the logo. We would also like to add that we offer:
Struggling with your finances?
- Learn to become debt free
- Discover the power of cash
- Control your money instead of it controlling you
Let us help you achieve a new level of financial freedom!
Also, we would like to have a "SPECIAL OFFER!: FREE 30 minute consultation"
Financial Planning

```html
<!DOCTYPE html>
<html lang="en">
<head>
<meta charset="utf-8">
<title>Clearpath Money Coaching – Business Card</title>
<link href="https://fonts.googleapis.com/css2?family=Open+Sans:wght@400;600;700&display=swap" rel="stylesheet">
<style>
  :root {
    --backdrop: #ecebe8;
    --card: #ffffff;
    --brand-green: #3f9a35;
    --ink: #1c1c1c;
    --rule: #333333;
    --tick: #6bb33a;
  }
  * { margin: 0; padding: 0; box-sizing: border-box; }
  html, body {
    width: 1200px; height: 1000px; overflow: hidden;
    background: var(--backdrop);
    font-family: "Open Sans", Arial, sans-serif;
    color: var(--ink);
  }
  .card {
    position: absolute; left: 265px; width: 666px; height: 397px;
    background: var(--card);
    box-shadow: 0 3px 10px rgba(0,0,0,0.18);
  }
  .card--front { top: 73px; }
  .card--back { top: 532px; }

  .holder { position: absolute; left: 33px; top: 108px - 73px; }
  .holder-name {
    position: absolute; left: 33px; top: 34px;
    font-size: 23px; font-weight: 700; color: var(--brand-green);
  }
  .holder-role { position: absolute; left: 33px; top: 63px; font-size: 16px; }

  .contact-list {
    position: absolute; right: 32px; top: 37px;
    list-style: none; text-align: right; font-size: 16px; line-height: 24.5px;
  }
  .contact-list li { display: flex; justify-content: flex-end; align-items: center; gap: 7px; }
  .contact-list svg { width: 14px; height: 14px; fill: var(--brand-green); }

  .address { position: absolute; right: 32px; top: 151px; text-align: right; font-size: 16px; line-height: 26px; }
  .divider { position: absolute; left: 361px; right: 32px; top: 220px; border-top: 1.5px solid var(--rule); }

  .brand {
    position: absolute; display: flex; align-items: center; gap: 10px;
    font-size: 24px; font-weight: 700; color: var(--brand-green); white-space: nowrap;
  }
  .brand-dot { width: 18px; height: 18px; border-radius: 50%; background: var(--brand-green); flex: none; }
  .card--front .brand { right: 32px; top: 290px; }
  .card--back .brand { left: 33px; top: 70px; }

  .offer { position: absolute; left: 33px; top: 314px; font-size: 16px; line-height: 22px; }
  .offer-label { font-weight: 600; }

  .pitch { position: absolute; left: 342px; top: 210px; width: 300px; font-size: 16px; line-height: 23px; }
  .pitch-title { font-weight: 700; margin-bottom: 3px; }
  .pitch-list { list-style: none; }
  .pitch-list li { position: relative; padding-left: 18px; }
  .pitch-list svg { position: absolute; left: 0; top: 6px; width: 14px; height: 12px; }
  .pitch-close { margin-top: 3px; }
</style>
</head>
<body>

<section class="card card--front">
  <h1 class="holder-name">Daniel Harrow</h1>
  <p class="holder-role">President</p>

  <ul class="contact-list">
    <li>+ 000 000 0000
      <svg viewBox="0 0 14 14" aria-hidden="true"><rect x="4" y="0" width="7" height="14" rx="1.5"/></svg></li>
    <li>+ 000 000 0000
      <svg viewBox="0 0 14 14" aria-hidden="true"><path d="M1 5c0-2 3-3 6-3s6 1 6 3v1h-3V5H4v1H1zM3 7h8l2 6H1z"/></svg></li>
    <li>hello@clearpathcoach.com
      <svg viewBox="0 0 14 14" aria-hidden="true"><path d="M0 3h14v9H0zM1 4l6 4 6-4z" fill-rule="evenodd"/></svg></li>
    <li>www.clearpathcoach.com
      <svg viewBox="0 0 14 14" aria-hidden="true"><circle cx="7" cy="7" r="6"/></svg></li>
  </ul>

  <p class="address">48 Elm Row St, Maple Grove, NY 1108<br>PO BOX 356, Maple Grove, NY 1108</p>
  <div class="divider"></div>

  <div class="brand"><span class="brand-dot"></span>Clearpath Money Coaching</div>

  <p class="offer"><span class="offer-label">SPECIAL OFFER!:</span><br>FREE 30 minute consultation</p>
</section>

<section class="card card--back">
  <div class="brand"><span class="brand-dot"></span>Clearpath Money Coaching</div>

  <div class="pitch">
    <p class="pitch-title">Struggling with your finances?</p>
    <ul class="pitch-list">
      <li><svg viewBox="0 0 14 12" aria-hidden="true"><path d="M1 6l4 4 8-9" fill="none" stroke="var(--tick)" stroke-width="2"/></svg>Learn to become debt free</li>
      <li><svg viewBox="0 0 14 12" aria-hidden="true"><path d="M1 6l4 4 8-9" fill="none" stroke="var(--tick)" stroke-width="2"/></svg>Discover the power of cash</li>
      <li><svg viewBox="0 0 14 12" aria-hidden="true"><path d="M1 6l4 4 8-9" fill="none" stroke="var(--tick)" stroke-width="2"/></svg>Control your money instead of it controlling you</li>
    </ul>
    <p class="pitch-close">Let us help you achieve a new level of financial freedom!</p>
  </div>
</section>

</body>
</html>
```